Hi Designers,

I will need 4 web pages designed. The web page looks like an App (if you click on the logo, or the icon on an iPad, it will take you to the website), but it is still a webpage.

Please check the attachment on this brief to understand what specific pages I need to be designed.

A .PSD (straight-up PhotoShop image) as final deliverable is fine, as long as you give us the exact “web color numbers”.

The design is for desktop and iPad but in a single unified web application, NOT separate web app and (native) iPad app.

Details:

Brightwater Policy Partners is developing a browser-based application for use on any mobile device or desktop. The app will be used by corporations to communicate with their employees regarding legal, regulatory and company requirements for conducting business. The app is known as “Harbor Guidance Portal.” When the user clicks on the icon for Harbor Guidance Portal, they will enter a site full of information that a company deems necessary for the employee to do his/her job. There are several content sections within the site, including a login page, training, policies, forms, news feeds and blogs.

The application has been built using Microsoft .NET, and fully supports CSS-type skinning; it uses traditional page layouts. We are seeking a product logo concept (image), a master application/desktop icon (image), as well as a full color scheme/theme/skin design for all areas of the application (header area, body text, menu bar, etc.) in the form of a CSS. The look should be clean, crisp and professional; nothing cartoony or whimsical. It should be easy to read and “airy”.

We have sketched prototypes for the basic application page layout that we can send as a next step of the process.
Updates

Screen shots have been uploaded to this project.  Please use them to guide your design.

Dear designers,

I apologize for the delay in providing feedback. My partners and I will provide feedback in a few days. Thank you for your patience.

Industry/Entity Type

Business

Font styles to use
Other font styles liked:
• see font on screen shots when uploaded

```html
<!DOCTYPE html>
<html lang="en">
<head>
<meta charset="utf-8">
<title>Harbor Guidance Portal</title>
<link href="https://fonts.googleapis.com/css2?family=Arimo:wght@400;700&display=swap" rel="stylesheet">
<style>
:root{
  --crimson:#d10c4f;
  --navy:#0d2a78;
  --orange:#f07b0c;
  --sky:#1b8fcc;
  --topbar:#0a8fcf;
  --page:#eeeeee;
  --line:#d6d6d6;
  --text:#555;
  --link:#0d2a78;
  --footer:#252525;
}
*{box-sizing:border-box;margin:0;padding:0}
html,body{width:1200px;height:1088px;overflow:hidden}
body{background:var(--page);font-family:"Arimo",Arial,sans-serif;color:var(--text);position:relative}
a{text-decoration:none;color:var(--link)}
.abs{position:absolute}
.topbar{left:0;top:0;width:1200px;height:6px;background:var(--topbar)}
.header{left:0;top:6px;width:1200px;height:110px;background:#fff;border-bottom:1px solid #ddd}
.brand-mark{left:283px;top:22px;width:40px;height:40px;border-radius:50%;background:var(--orange)}
.brand-name{left:199px;top:82px;font-size:20px;color:var(--crimson)}
.nav{left:608px;top:20px;height:29px;display:flex;background:#fff;border:1px solid #ccc;box-shadow:0 1px 2px rgba(0,0,0,.1)}
.nav a{display:flex;align-items:center;gap:7px;padding:0 17px;font-size:11.5px;font-weight:700;color:var(--crimson);border-right:1px solid #ccc}
.nav a:last-child{border-right:0;padding:0 18px}
.nav svg{width:12px;height:12px;fill:var(--navy)}
.points{left:818px;top:67px;width:38px;height:23px;background:var(--orange);color:#fff;font-size:11px;display:flex;align-items:center;justify-content:center;box-shadow:0 1px 2px rgba(0,0,0,.3)}
.points-dot{left:851px;top:63px;width:10px;height:10px;border-radius:50%;background:var(--navy);color:#fff;font-size:7px;text-align:center;line-height:10px}
.user{left:879px;top:66px;width:120px;height:24px;border:1px solid #ccc;background:#fafafa;display:flex;align-items:center;font-size:10px;color:var(--crimson)}
.avatar{width:22px;height:22px;background:linear-gradient(135deg,#8a6b5c,#c9b3a3);margin-right:8px}
.user .caret{margin-left:auto;width:20px;height:22px;border-left:1px solid #ccc;display:flex;align-items:center;justify-content:center}
.welcome{left:200px;top:140px;width:800px;height:43px;background:var(--crimson);color:#fff;font-size:20px;padding:10px 13px}
.hero-img{left:200px;top:194px;width:218px;height:130px;background:linear-gradient(180deg,#eef3f6,#bcd8e2 55%,#d9e4e8);border:1px solid #ccc;box-shadow:0 1px 3px rgba(0,0,0,.25)}
.intro{left:442px;top:200px;width:530px;font-size:9.7px;line-height:14.4px;color:var(--text)}
.intro a{display:block;margin-top:3px;font-size:10px}
.card{top:360px;width:244px;height:240px;background:#fff;border:1px solid var(--line);overflow:hidden}
.card-head{height:47px;display:flex;align-items:center;padding:0 10px;color:#fff;font-size:15px;gap:12px}
.card-head .go{margin-left:auto;width:24px;height:24px;border-radius:50%;border:1px solid rgba(255,255,255,.6);display:flex;align-items:center;justify-content:center}
.card-head svg.ic{width:24px;height:24px;fill:#fff}
.news .card-head{background:var(--navy)}
.blog .card-head{background:var(--orange)}
.form .card-head{background:var(--sky)}
.item{margin:0 6px 0 7px;padding:12px 0 6px;border-bottom:1px solid #e3e3e3;font-size:9.3px;line-height:14.4px}
.item:last-child{border-bottom:0}
.meta{display:flex;align-items:center;gap:5px;margin-top:2px;font-size:10px}
.meta a{color:var(--link)}
.meta svg{width:11px;height:11px}
.meta .gap{width:10px}
.blog-item{display:flex;gap:12px;margin:0 4px;padding:7px 0;border-bottom:1px solid #e3e3e3;font-size:9.5px;line-height:14.4px}
.blog-item:last-child{border-bottom:0}
.thumb{flex:none;width:52px;height:48px;border:1px solid #ccc;background:linear-gradient(90deg,#3a8f3a,#e8d21b 35%,#d22 60%,#2c4ad0);}
.sec-title{top:637px;font-size:20px;color:var(--crimson)}
.box{top:672px;width:244px;height:108px;background:#fff;border:1px solid var(--line);padding:14px 7px;font-size:9.5px;line-height:14.4px}
.box .meta{margin-top:18px}
.report{left:757px;top:672px;width:243px;height:108px;background:#fff;border:1px solid var(--line);display:flex}
.report .col{flex:1;min-width:0;padding:0 0 0 10px}
.report .col+ .col{border-left:1px solid var(--line)}
.report h4{font-size:11px;color:var(--navy);text-align:center;height:17px;line-height:17px;border-bottom:1px solid var(--line);margin-left:-10px}
.report dl{display:grid;grid-template-columns:64px 1fr;font-size:9.5px;color:#111;row-gap:5px;margin-top:4px}
.report dd{color:#1144cc}
.stars{display:flex;gap:1px}
.stars svg{width:8px;height:8px}
.links{left:200px;top:848px;width:801px;height:124px;background:#fff;border:1px solid var(--line);display:grid;grid-template-columns:139px 137px 137px 137px 143px 1fr;padding:14px 0 0 21px;row-gap:11px}
.links a{font-size:12px;font-weight:700;display:flex;align-items:center;gap:8px;height:14px}
.links a::before{content:"";width:9px;height:9px;border-radius:50%;background:radial-gradient(circle at 35% 35%,#888,#111)}
.footer{left:0;top:997px;width:1200px;height:91px;background:var(--footer);color:#fff}
.foot-nav{left:200px;top:20px;font-size:10px;display:flex;gap:5px}
.foot-nav a{color:#fff}
.copy{left:199px;top:54px;font-size:10px}
.social{left:899px;top:31px;display:flex;gap:2px}
.social span{width:24px;height:24px;border-radius:50%}
</style>
</head>
<body>
<div class="abs topbar"></div>
<header class="abs header">
</header>
<div class="abs brand-mark"></div>
<div class="abs brand-name">Harbor Guidance Portal</div>
<nav class="abs nav">
  <a href="#"><svg viewBox="0 0 12 12"><path d="M6 1 0 6h2v5h3V8h2v3h3V6h2z"/></svg>Home</a>
  <a href="#"><svg viewBox="0 0 12 12"><rect y="2" width="12" height="1.6"/><rect y="5.2" width="12" height="1.6"/><rect y="8.4" width="12" height="1.6"/></svg>Menu</a>
  <a href="#"><svg viewBox="0 0 12 12"><circle cx="6" cy="5" r="4"/><path d="M3 8l-1.5 4 2-1 1 1.5L6 9zM9 8l1.5 4-2-1-1 1.5L6 9z"/></svg>Game</a>
  <a href="#"><svg viewBox="0 0 12 12"><path d="M5.3 1.2A5 5 0 1 0 10.8 6.7H5.3z"/><path d="M6.5 0v5.5H12A5.5 5.5 0 0 0 6.5 0z"/></svg>Hcp 360</a>
  <a href="#" aria-label="Search"><svg viewBox="0 0 12 12"><path d="M5 1a4 4 0 1 0 2.4 7.2L10.6 11.4l.9-.9L8.2 7.3A4 4 0 0 0 5 1zm0 1.4a2.6 2.6 0 1 1 0 5.2 2.6 2.6 0 0 1 0-5.2z"/></svg></a>
</nav>
<div class="abs points">420</div>
<div class="abs points-dot">1</div>
<div class="abs user"><span class="avatar" role="img" aria-label="User avatar"></span>Dana Reyes<span class="caret"><svg width="6" height="4" viewBox="0 0 6 4"><path d="M0 0h6L3 4z" fill="#777"/></svg></span></div>

<div class="abs welcome">Welcome To Harbor Guidance Portal</div>
<div class="abs hero-img" role="img" aria-label="Laboratory flasks with blue and green liquid"></div>
<p class="abs intro">Lorem ipsum dolor sit amet, consectetur adipisicing elit, sed do eiusmod tempor incididunt ut labore et dolore magna aliqua. Ut...Lorem ipsum dolor sit amet, consectetur adipisicing elit, sed do eiusmod tempor incididunt ut labore et dolore magna Lorem ipsum dolor sit amet, consectetur adipisicing elit, sed do eiusmod tempor incididunt ut labore et dolore Lorem ipsum dolor sit amet, consectetur adipisicing elit, sed do eiusmod tempor incididunt ut labore et Lorem ipsum dolor sit amet, con-sectetur adipisicing elit, sed do eiusmod tempor incididunt ut labore Lorem ipsum dolor sit amet, consectetur adipisicing elit, ut labore et dolore magna aliqua. Ut...labore et doloLorem ipsum dolor sit amet, consectetur adipisicing elit, sed do eiusmod tempor incididunt ut labore et dolore magna aliqua. Ut...<a href="#">Read more...</a></p>

<!-- news -->
<section class="abs card news" style="left:200px">
  <div class="card-head"><svg class="ic" viewBox="0 0 24 24"><path d="M3 3h18v18H3zm2 2v14h14V5zm2 2h4v4H7zm6 0h4v1.5h-4zm0 3h4v1.5h-4zM7 13h10v1.5H7zm0 3h10v1.5H7z"/></svg>Compliance News<span class="go"><svg width="6" height="9" viewBox="0 0 6 9"><path d="M1 1l3.5 3.5L1 8" stroke="#fff" stroke-width="1.5" fill="none"/></svg></span></div>
  <div class="item">Lorem ipsum dolor sit amet, consectetur adipisicing elit, sed do eiusmod tempor incididunt ut labore et do<div class="meta"><svg viewBox="0 0 11 11"><rect x=".5" y="1.5" width="10" height="9" fill="none" stroke="#333"/><rect x="2" y="4" width="7" height="5" fill="#333" opacity=".5"/></svg><a href="#">19-Nov-2103</a><span class="gap"></span><svg viewBox="0 0 11 11"><path d="M0 5h2v6H0zm3 0 3-5c1 0 1.4.7 1 2L6.5 4H10c1 0 1 1 .8 1.6L9.5 10c-.2.6-.6 1-1.2 1H3z" fill="#111"/></svg><a href="#">Like</a><span class="gap"></span><svg viewBox="0 0 11 11"><path d="M5.5 10 1 5.5A2.6 2.6 0 0 1 5.5 2a2.6 2.6 0 0 1 4.5 3.5z" fill="#111"/></svg><a href="#">Rating</a></div></div>
  <div class="item">Lorem ipsum dolor sit amet, consectetur adipisicing elit, sed do eiusmod tempor incididunt ut labore et do<div class="meta"><svg viewBox="0 0 11 11"><rect x=".5" y="1.5" width="10" height="9" fill="none" stroke="#333"/><rect x="2" y="4" width="7" height="5" fill="#333" opacity=".5"/></svg><a href="#">19-Nov-2103</a><span class="gap"></span><svg viewBox="0 0 11 11"><path d="M0 5h2v6H0zm3 0 3-5c1 0 1.4.7 1 2L6.5 4H10c1 0 1 1 .8 1.6L9.5 10c-.2.6-.6 1-1.2 1H3z" fill="#111"/></svg><a href="#">Like</a><span class="gap"></span><svg viewBox="0 0 11 11"><path d="M5.5 10 1 5.5A2.6 2.6 0 0 1 5.5 2a2.6 2.6 0 0 1 4.5 3.5z" fill="#111"/></svg><a href="#">Rating</a></div></div>
  <div class="item">Lorem ipsum dolor sit amet, consectetur adipisicing elit, sed do eiusmod tempor incididunt ut labore et do<div class="meta"><svg viewBox="0 0 11 11"><rect x=".5" y="1.5" width="10" height="9" fill="none" stroke="#333"/><rect x="2" y="4" width="7" height="5" fill="#333" opacity=".5"/></svg><a href="#">19-Nov-2103</a><span class="gap"></span><svg viewBox="0 0 11 11"><path d="M0 5h2v6H0zm3 0 3-5c1 0 1.4.7 1 2L6.5 4H10c1 0 1 1 .8 1.6L9.5 10c-.2.6-.6 1-1.2 1H3z" fill="#111"/></svg><a href="#">Like</a><span class="gap"></span><svg viewBox="0 0 11 11"><path d="M5.5 10 1 5.5A2.6 2.6 0 0 1 5.5 2a2.6 2.6 0 0 1 4.5 3.5z" fill="#111"/></svg><a href="#">Rating</a></div></div>
</section>

<!-- blog -->
<section class="abs card blog" style="left:478px">
  <div class="card-head"><svg class="ic" viewBox="0 0 24 24"><path d="M2 9h4l10-6v18L6 15H2zm5 7h3l1 5H8z"/></svg>Compliance Blog<span class="go"><svg width="6" height="9" viewBox="0 0 6 9"><path d="M1 1l3.5 3.5L1 8" stroke="#fff" stroke-width="1.5" fill="none"/></svg></span></div>
  <div class="blog-item"><span class="thumb" role="img" aria-label="Colored liquid flasks"></span><p>Lorem ipsum dolor sit amet, consecte-tur adipisicing elit, sed do eiusmod tempor incididunt ut labore et do</p></div>
  <div class="blog-item"><span class="thumb" role="img" aria-label="Colored liquid flasks"></span><p>Lorem ipsum dolor sit amet, consecte-tur adipisicing elit, sed do eiusmod tempor incididunt ut labore et do</p></div>
  <div class="blog-item"><span class="thumb" role="img" aria-label="Colored liquid flasks"></span><p>Lorem ipsum dolor sit amet, consecte-tur adipisicing elit, sed do eiusmod tempor incididunt ut labore et do</p></div>
</section>

<!-- form -->
<section class="abs card form" style="left:756px">
  <div class="card-head"><svg class="ic" viewBox="0 0 24 24"><path d="M3 10h9v2H5v8h10v-5h2v7H3z"/><path d="M20 2l2 2L10 16l-3 1 1-3z"/></svg>Form<span class="go"><svg width="6" height="9" viewBox="0 0 6 9"><path d="M1 1l3.5 3.5L1 8" stroke="#fff" stroke-width="1.5" fill="none"/></svg></span></div>
  <div class="item">Lorem ipsum dolor sit amet, consectetur adipisicing elit, sed do eiusmod tempor incididunt ut labore et do<div class="meta"><svg viewBox="0 0 11 11"><rect x=".5" y="1.5" width="10" height="9" fill="none" stroke="#333"/><rect x="2" y="4" width="7" height="5" fill="#333" opacity=".5"/></svg><a href="#">19-Nov-2103</a><span class="gap"></span><svg viewBox="0 0 11 11"><path d="M0 5h2v6H0zm3 0 3-5c1 0 1.4.7 1 2L6.5 4H10c1 0 1 1 .8 1.6L9.5 10c-.2.6-.6 1-1.2 1H3z" fill="#111"/></svg><a href="#">Like</a><span class="gap"></span><svg viewBox="0 0 11 11"><path d="M5.5 10 1 5.5A2.6 2.6 0 0 1 5.5 2a2.6 2.6 0 0 1 4.5 3.5z" fill="#111"/></svg><a href="#">Rating</a></div></div>
  <div class="item">Lorem ipsum dolor sit amet, consectetur adipisicing elit, sed do eiusmod tempor incididunt ut labore et do<div class="meta"><svg viewBox="0 0 11 11"><rect x=".5" y="1.5" width="10" height="9" fill="none" stroke="#333"/><rect x="2" y="4" width="7" height="5" fill="#333" opacity=".5"/></svg><a href="#">19-Nov-2103</a><span class="gap"></span><svg viewBox="0 0 11 11"><path d="M0 5h2v6H0zm3 0 3-5c1 0 1.4.7 1 2L6.5 4H10c1 0 1 1 .8 1.6L9.5 10c-.2.6-.6 1-1.2 1H3z" fill="#111"/></svg><a href="#">Like</a><span class="gap"></span><svg viewBox="0 0 11 11"><path d="M5.5 10 1 5.5A2.6 2.6 0 0 1 5.5 2a2.6 2.6 0 0 1 4.5 3.5z" fill="#111"/></svg><a href="#">Rating</a></div></div>
  <div class="item">Lorem ipsum dolor sit amet, consectetur adipisicing elit, sed do eiusmod tempor incididunt ut labore et do<div class="meta"><svg viewBox="0 0 11 11"><rect x=".5" y="1.5" width="10" height="9" fill="none" stroke="#333"/><rect x="2" y="4" width="7" height="5" fill="#333" opacity=".5"/></svg><a href="#">19-Nov-2103</a><span class="gap"></span><svg viewBox="0 0 11 11"><path d="M0 5h2v6H0zm3 0 3-5c1 0 1.4.7 1 2L6.5 4H10c1 0 1 1 .8 1.6L9.5 10c-.2.6-.6 1-1.2 1H3z" fill="#111"/></svg><a href="#">Like</a><span class="gap"></span><svg viewBox="0 0 11 11"><path d="M5.5 10 1 5.5A2.6 2.6 0 0 1 5.5 2a2.6 2.6 0 0 1 4.5 3.5z" fill="#111"/></svg><a href="#">Rating</a></div></div>
</section>

<h2 class="abs sec-title" style="left:199px;font-weight:400">FAQ’S</h2>
<h2 class="abs sec-title" style="left:479px;font-weight:400">Document Library</h2>
<h2 class="abs sec-title" style="left:758px;font-weight:400">Reports</h2>

<div class="abs box" style="left:200px">Lorem ipsum dolor sit amet, consectetur adipisicing elit, sed do eiusmod tempor incididunt ut labore et do Lorem ipsum dolor sit amet, consectetur adipisicing elit, sed do eiusmod tempor incididunt ut labore et do<div class="meta"><svg viewBox="0 0 11 11"><rect x=".5" y="1.5" width="10" height="9" fill="none" stroke="#333"/><rect x="2" y="4" width="7" height="5" fill="#333" opacity=".5"/></svg><a href="#">19-Nov-2103</a><span class="gap"></span><svg viewBox="0 0 11 11"><path d="M0 5h2v6H0zm3 0 3-5c1 0 1.4.7 1 2L6.5 4H10c1 0 1 1 .8 1.6L9.5 10c-.2.6-.6 1-1.2 1H3z" fill="#111"/></svg><a href="#">Like</a><span class="gap"></span><svg viewBox="0 0 11 11"><path d="M5.5 10 1 5.5A2.6 2.6 0 0 1 5.5 2a2.6 2.6 0 0 1 4.5 3.5z" fill="#111"/></svg><a href="#">Rating</a></div></div>
<div class="abs box" style="left:479px">Lorem ipsum dolor sit amet, consectetur adipisicing elit, sed do eiusmod tempor incididunt ut labore et do Lorem ipsum dolor sit amet, consectetur adipisicing elit, sed do eiusmod tempor incididunt ut labore et do<div class="meta"><svg viewBox="0 0 11 11"><rect x=".5" y="1.5" width="10" height="9" fill="none" stroke="#333"/><rect x="2" y="4" width="7" height="5" fill="#333" opacity=".5"/></svg><a href="#">19-Nov-2103</a><span class="gap"></span><svg viewBox="0 0 11 11"><path d="M0 5h2v6H0zm3 0 3-5c1 0 1.4.7 1 2L6.5 4H10c1 0 1 1 .8 1.6L9.5 10c-.2.6-.6 1-1.2 1H3z" fill="#111"/></svg><a href="#">Like</a><span class="gap"></span><svg viewBox="0 0 11 11"><path d="M5.5 10 1 5.5A2.6 2.6 0 0 1 5.5 2a2.6 2.6 0 0 1 4.5 3.5z" fill="#111"/></svg><a href="#">Rating</a></div></div>

<div class="abs report">
  <div class="col"><h4>Player 1</h4><dl><dt>Players :</dt><dd>Alex</dd><dt>Ranking :</dt><dd>2</dd><dt>Score :</dt><dd>120</dd><dt>Percentage :</dt><dd>78</dd><dt>Rating :</dt><dd class="stars"><svg viewBox="0 0 10 10"><path d="M5 0l1.5 3.3 3.5.4-2.6 2.4.7 3.5L5 7.8 1.9 9.6l.7-3.5L0 3.7l3.5-.4z" fill="#e0a51b"/></svg><svg viewBox="0 0 10 10"><path d="M5 0l1.5 3.3 3.5.4-2.6 2.4.7 3.5L5 7.8 1.9 9.6l.7-3.5L0 3.7l3.5-.4z" fill="#e0a51b"/></svg><svg viewBox="0 0 10 10"><path d="M5 0l1.5 3.3 3.5.4-2.6 2.4.7 3.5L5 7.8 1.9 9.6l.7-3.5L0 3.7l3.5-.4z" fill="#e0a51b"/></svg><svg viewBox="0 0 10 10"><path d="M5 0l1.5 3.3 3.5.4-2.6 2.4.7 3.5L5 7.8 1.9 9.6l.7-3.5L0 3.7l3.5-.4z" fill="#ccc"/></svg><svg viewBox="0 0 10 10"><path d="M5 0l1.5 3.3 3.5.4-2.6 2.4.7 3.5L5 7.8 1.9 9.6l.7-3.5L0 3.7l3.5-.4z" fill="#ccc"/></svg></dd></dl></div>
  <div class="col"><h4>Player 2</h4><dl><dt>Players :</dt><dd>Alex</dd><dt>Ranking :</dt><dd>2</dd><dt>Score :</dt><dd>120</dd><dt>Percentage :</dt><dd>78</dd><dt>Rating :</dt><dd class="stars"><svg viewBox="0 0 10 10"><path d="M5 0l1.5 3.3 3.5.4-2.6 2.4.7 3.5L5 7.8 1.9 9.6l.7-3.5L0 3.7l3.5-.4z" fill="#e0a51b"/></svg><svg viewBox="0 0 10 10"><path d="M5 0l1.5 3.3 3.5.4-2.6 2.4.7 3.5L5 7.8 1.9 9.6l.7-3.5L0 3.7l3.5-.4z" fill="#e0a51b"/></svg><svg viewBox="0 0 10 10"><path d="M5 0l1.5 3.3 3.5.4-2.6 2.4.7 3.5L5 7.8 1.9 9.6l.7-3.5L0 3.7l3.5-.4z" fill="#e0a51b"/></svg><svg viewBox="0 0 10 10"><path d="M5 0l1.5 3.3 3.5.4-2.6 2.4.7 3.5L5 7.8 1.9 9.6l.7-3.5L0 3.7l3.5-.4z" fill="#ccc"/></svg><svg viewBox="0 0 10 10"><path d="M5 0l1.5 3.3 3.5.4-2.6 2.4.7 3.5L5 7.8 1.9 9.6l.7-3.5L0 3.7l3.5-.4z" fill="#ccc"/></svg></dd></dl></div>
</div>

<h2 class="abs sec-title" style="left:199px;top:813px;font-weight:400">Revalent Links</h2>
<nav class="abs links">
  <a href="#">Computer</a><a href="#">Apps</a><a href="#">About Us</a><a href="#">Photos</a><a href="#">Documents</a><a href="#">Bills</a>
  <a href="#">Hardisk</a><a href="#">Books</a><a href="#">Services</a><a href="#">Funny</a><a href="#">Library</a><a href="#">Money</a>
  <a href="#">Game</a><a href="#">Keyboard</a><a href="#">Products</a><a href="#">Reports</a><a href="#">Blog</a><a href="#">Labs</a>
  <a href="#">Labs</a><a href="#">Home</a><a href="#">Gallery</a><a href="#">FAQ</a><a href="#">Form</a><a href="#">Contact Us</a>
</nav>

<footer class="abs footer">
  <nav class="abs foot-nav"><a href="#">Home</a>|<a href="#">About us</a>|<a href="#">Counselling</a>|<a href="#">Workshop</a>|<a href="#">Contact us</a></nav>
  <p class="abs copy">Content copyright 2013. HGP. All rights reserved.</p>
  <div class="abs social"><span style="background:#3b5998"></span><span style="background:#1da1f2"></span><span style="background:#dd4b39"></span><span style="background:#0e76a8"></span></div>
</footer>
</body>
</html>
```